HearthMile business card and stationary design

We are looking for a simple yet elegant design for our mortgage company business card and stationary.

The card should include:
Name (Marcus Pell)
Title (CEO)
Phone Number (555-555-0182)
Address (48 Birchwell Court, Suite 314, Fernmoor, ST 00000)
Email (email@hearthmile.example)
"NMLS" i.e. (NMLS 61947)
"Company NMLS" (Company NMLS 274615)

Contact Information for Business Card

See above

```html
<!DOCTYPE html>
<html lang="en">
<head>
<meta charset="utf-8">
<title>HearthMile Business Card</title>
<link rel="stylesheet" href="https://fonts.googleapis.com/css2?family=Montserrat:wght@500;600&family=Roboto:wght@400&display=swap">
<style>
  :root {
    --page-bg: #e4e4e4;
    --brand-blue: #00a6e6;
    --brand-navy: #17212c;
    --ink: #1b1f24;
    --card-white: #ffffff;
    --grad-top: #00a3df;
    --grad-mid: #0c6690;
    --grad-bottom: #1a2430;
  }
  html, body {
    margin: 0;
    padding: 0;
    width: 1200px;
    height: 900px;
    overflow: hidden;
    background: var(--page-bg);
  }
  .canvas {
    position: relative;
    width: 1200px;
    height: 900px;
  }
  .card {
    position: absolute;
    top: 216px;
    width: 309px;
    height: 501px;
    box-sizing: border-box;
  }
  .card-front {
    left: 279px;
    border-radius: 0 60px 0 60px;
    background: linear-gradient(205deg, var(--grad-top) 0%, var(--grad-mid) 45%, var(--grad-bottom) 100%);
  }
  .card-back {
    left: 617px;
    border-radius: 60px 0 60px 0;
    background: var(--card-white);
  }
  .wordmark {
    position: absolute;
    margin: 0;
    font-family: "Montserrat", sans-serif;
    font-weight: 500;
    letter-spacing: -0.5px;
    line-height: 1;
    white-space: nowrap;
  }
  .card-front .wordmark {
    left: 50px;
    top: 408px;
    font-size: 43px;
    color: var(--card-white);
  }
  .card-back .wordmark {
    left: 46px;
    top: 118px;
    font-size: 44px;
    color: var(--brand-navy);
  }
  .contact-block {
    position: absolute;
    left: 32px;
    top: 270px;
    font-family: "Roboto", sans-serif;
    color: var(--ink);
  }
  .person-name {
    margin: 0;
    font-family: "Montserrat", sans-serif;
    font-weight: 600;
    font-size: 21px;
    line-height: 1;
    color: var(--brand-navy);
  }
  .person-name .surname { color: var(--brand-blue); }
  .person-title {
    margin: 2px 0 0;
    font-size: 14px;
    line-height: 1.1;
  }
  .contact-list {
    list-style: none;
    margin: 14px 0 0;
    padding: 0;
    font-size: 14px;
    line-height: 18px;
  }
  .contact-list li {
    display: flex;
    align-items: flex-start;
    gap: 4px;
  }
  .contact-list .icon {
    width: 13px;
    height: 13px;
    margin-top: 3px;
    flex: none;
    fill: var(--brand-blue);
  }
  .accent { color: var(--brand-blue); }
  .address { margin-top: 12px; }
  .licenses {
    margin: 12px 0 0;
    font-size: 14px;
    line-height: 18px;
  }
  .licenses p { margin: 0; }
</style>
</head>
<body>
<main class="canvas">
  <section class="card card-front" aria-label="Card front">
    <p class="wordmark">HearthMile</p>
  </section>

  <section class="card card-back" aria-label="Card back">
    <p class="wordmark">HearthMile</p>

    <div class="contact-block">
      <h1 class="person-name">Marcus <span class="surname">Pell</span></h1>
      <p class="person-title">CEO</p>

      <ul class="contact-list">
        <li>
          <svg class="icon" viewBox="0 0 24 24" aria-hidden="true"><path d="M6.6 10.8c1.4 2.8 3.8 5.1 6.6 6.6l2.2-2.2c.3-.3.7-.4 1-.2 1.1.4 2.3.6 3.6.6.6 0 1 .4 1 1V20c0 .6-.4 1-1 1C10.6 21 3 13.4 3 4c0-.6.4-1 1-1h3.5c.6 0 1 .4 1 1 0 1.3.2 2.5.6 3.6.1.3 0 .7-.2 1z"/></svg>
          <span>555-555-0182</span>
        </li>
        <li>
          <svg class="icon" viewBox="0 0 24 24" aria-hidden="true"><path d="M2 5h20v14H2z" fill="var(--brand-blue)"/><path d="M2 5l10 8 10-8" fill="none" stroke="#fff" stroke-width="1.6"/></svg>
          <span>email@hearthmile.example</span>
        </li>
        <li>
          <svg class="icon" viewBox="0 0 24 24" aria-hidden="true"><g fill="none" stroke="var(--brand-blue)" stroke-width="2"><circle cx="12" cy="12" r="9.5"/><ellipse cx="12" cy="12" rx="4.5" ry="9.5"/><path d="M2.5 12h19M4.5 7h15M4.5 17h15"/></g></svg>
          <span>www.<span class="accent">hearthmile</span>.example</span>
        </li>
        <li class="address">
          <svg class="icon" viewBox="0 0 24 24" aria-hidden="true"><path d="M12 1C7.6 1 4 4.6 4 9c0 6 8 14 8 14s8-8 8-14c0-4.4-3.6-8-8-8zm0 11a3 3 0 1 1 0-6 3 3 0 0 1 0 6z"/></svg>
          <span>48 Birchwell Court, Suite 314<br>Fernmoor, ST 00000</span>
        </li>
      </ul>

      <div class="licenses">
        <p><span class="accent">NMLS</span> 61947</p>
        <p><span class="accent">Company NMLS</span> 274615</p>
      </div>
    </div>
  </section>
</main>
</body>
</html>
```